Brightmill Data Works

Our company is about IT hardwares and IT solutions. IT hardware such as PC, RAMS, storage and servers. IT solutions such as project management, BA. We are also selling new technology too.

Target Market(s)

Consumer, Small to Medium Business, Corporate

Requirements
Must have
• The business card must have the following:
• Name:
• Title:
• Contact Number:
• Email address:
• Website:
• Color: Must match the logo color upgrade

```html
<!DOCTYPE html>
<html lang="en">
<head>
<meta charset="utf-8">
<title>Brightmill Data Works – Business Card</title>
<link rel="stylesheet" href="https://fonts.googleapis.com/css2?family=Open+Sans:wght@400;600;700&display=swap">
<style>
  :root {
    --backdrop: #666666;
    --card-white: #ffffff;
    --charcoal: #474747;
    --ink: #3d3d3d;
    --amber-light: #dc9842;
    --amber-deep: #c3672a;
    --amber: #d4852f;
    --text-light: #ffffff;
  }
  * { margin: 0; padding: 0; box-sizing: border-box; }
  html, body {
    width: 1200px;
    height: 802px;
    overflow: hidden;
    background: var(--backdrop);
    font-family: "Open Sans", Arial, sans-serif;
  }
  .canvas {
    position: relative;
    width: 1200px;
    height: 802px;
  }
  .card {
    position: absolute;
    top: 274px;
    width: 443px;
    height: 265px;
    overflow: hidden;
  }
  .card-front {
    left: 135px;
    background: linear-gradient(180deg, var(--amber-light) 0%, var(--amber-deep) 100%);
  }
  .front-panel {
    position: absolute;
    left: 0;
    top: 0;
    width: 96px;
    height: 100%;
    background: var(--charcoal);
  }
  .holder {
    position: absolute;
    right: 26px;
    top: 66px;
    text-align: right;
    color: var(--text-light);
  }
  .holder-name {
    font-size: 16.5px;
    font-weight: 600;
    line-height: 1.1;
    letter-spacing: 0.1px;
  }
  .holder-title {
    font-size: 13px;
    font-weight: 400;
    line-height: 1.2;
  }
  .contact-list {
    position: absolute;
    right: 26px;
    top: 148px;
    list-style: none;
    color: var(--text-light);
    font-size: 13px;
    line-height: 16px;
    text-align: right;
  }
  .contact-item {
    display: flex;
    align-items: center;
    justify-content: flex-end;
    gap: 4px;
  }
  .contact-icon {
    width: 10px;
    height: 10px;
    flex: none;
  }
  .card-back {
    left: 624px;
    background: var(--card-white);
    display: flex;
    flex-direction: column;
    align-items: center;
    justify-content: center;
    gap: 18px;
  }
  .brand-mark {
    width: 22px;
    height: 22px;
    background: var(--amber);
  }
  .brand-name {
    font-size: 27px;
    font-weight: 700;
    color: var(--ink);
    letter-spacing: 0.3px;
  }
</style>
</head>
<body>
<main class="canvas">
  <section class="card card-front" aria-label="Business card front">
    <div class="front-panel"></div>
    <div class="holder">
      <p class="holder-name">DANIEL HARROW</p>
      <p class="holder-title">Managing Director</p>
    </div>
    <ul class="contact-list">
      <li class="contact-item">044-555 018 342
        <svg class="contact-icon" viewBox="0 0 10 10" aria-hidden="true"><path fill="#fff" d="M1 3.2C1 2 2.6 1.2 5 1.2S9 2 9 3.2V4H7V3H3v1H1z M2.2 5h5.6l.8 3.8H1.4z"/></svg>
      </li>
      <li class="contact-item">info@brightmilldata.com
        <svg class="contact-icon" viewBox="0 0 10 10" aria-hidden="true"><rect x="0.5" y="2" width="9" height="6.5" fill="#fff"/><path d="M0.8 2.3 5 5.6 9.2 2.3" fill="none" stroke="#c8732d" stroke-width="0.9"/></svg>
      </li>
      <li class="contact-item">www.brightmilldata.com
        <svg class="contact-icon" viewBox="0 0 10 10" aria-hidden="true"><circle cx="5" cy="5" r="4.6" fill="#fff"/><path d="M3 3.2c1 .2 1.6 1 1.3 1.9L3.4 6.3M6.5 6.8c.3-1 1.2-1.3 2-1" fill="none" stroke="#c8732d" stroke-width="1"/></svg>
      </li>
    </ul>
  </section>

  <section class="card card-back" aria-label="Business card back">
    <div class="brand-mark"></div>
    <p class="brand-name">Brightmill Data Works</p>
  </section>
</main>
</body>
</html>
```